I need a business card designed using the logo provided either vertical or horizontal......Harbourline Property Group is an Australian based real estate company that caters for the upper end of the market so the design of the business card "must reflect" the companies image!!
Colour combinations are optional but "must be realistic" and must be able to be accurately useable CMYK colours.
Please consider that any colours used "must be able to be used" and be suitable in following designs for "pull out banner signs" and "real estate signs".
The colours and the font in the attached designs are for example and other combinations are encouraged.
Target Market(s)
The High End of the Australian real estate market
Industry/Entity Type
Business
Contact Information for Business Card
Logo - Business Name - Director + Licensed Real Estate Agent - Mobile Number (Cell Phone) - Business Number - Fax - Email Address - Web address
Requirements
Must have
- Designs and colours (CMYK) that can easily be interpreted by an Australian printer.
Nice to have
- Some alternative ideas on colour and font..........the ones provided are ok and have been provided as an example but I am looking for alternative ideas
Should not have
- Loud, overly bright colours. Designs that do not reflect the professional standards of the business.
- Designs that look good on a computer monitor but can not be re-created on a printing press.............this is most important when it comes to shading etc.

```html
<!DOCTYPE html>
<html lang="en">
<head>
<meta charset="utf-8">
<title>Harbourline Property Group — Business Card</title>
<link href="https://fonts.googleapis.com/css2?family=Didact+Gothic&family=Signika:wght@600&display=swap" rel="stylesheet">
<style>
  :root {
    --gold: #b07d2b;
    --tan: #d2c192;
    --ink: #231f20;
    --card: #ffffff;
    --backdrop: #efe9df;
  }
  * { box-sizing: border-box; margin: 0; padding: 0; }
  html, body {
    width: 1189px; height: 1200px; overflow: hidden;
    background: var(--backdrop);
    font-family: "Didact Gothic", "Helvetica Neue", Arial, sans-serif;
    color: var(--ink);
  }
  .card {
    position: absolute;
    left: 171px; width: 856px; height: 487px;
    background: var(--card);
    border-radius: 22px;
    box-shadow: 0 2px 6px rgba(0,0,0,0.12);
  }
  .card--front { top: 68px; }
  .card--back { top: 627px; }

  /* Brand name block */
  .brand {
    position: absolute;
    display: flex; align-items: center; gap: 26px;
    color: var(--ink);
    font-family: "Didact Gothic", Arial, sans-serif;
    font-weight: 400;
  }
  .brand__mark { width: 22px; height: 22px; background: var(--gold); flex: none; }
  .brand__name { line-height: 1.08; }
  .card--front .brand {
    left: 0; right: 0; top: 190px; justify-content: center;
    font-size: 48px; letter-spacing: 1px;
  }

  .web-row {
    position: absolute; left: 126px; right: 126px; top: 402px;
    display: flex; align-items: center; gap: 22px;
  }
  .web-row__rule { flex: 1; height: 2px; }
  .web-row__rule--left { background: linear-gradient(to right, rgba(176,125,43,0), var(--gold)); }
  .web-row__rule--right { background: linear-gradient(to left, rgba(176,125,43,0), var(--gold)); }
  .web-row__url { font-size: 26px; letter-spacing: 1.5px; white-space: nowrap; }

  /* Back */
  .card--back .brand {
    left: 36px; width: 370px; top: 150px;
    flex-direction: column; gap: 18px; text-align: center;
    font-size: 38px;
  }
  .divider {
    position: absolute; left: 429px; top: 60px; width: 2px; height: 367px;
    background: linear-gradient(to bottom, rgba(176,125,43,0), var(--gold) 12%, var(--gold) 88%, rgba(176,125,43,0));
  }
  .contact { position: absolute; left: 479px; top: 66px; right: 30px; }
  .contact__name {
    font-family: "Signika", Arial, sans-serif; font-weight: 600;
    color: var(--gold); font-size: 29px; letter-spacing: 0.5px; line-height: 1;
  }
  .contact__role { font-size: 18px; letter-spacing: 1px; line-height: 23px; margin-top: 8px; }
  .contact__address { font-size: 20px; letter-spacing: 1px; line-height: 26px; margin-top: 22px; }
  .contact__list { list-style: none; margin-top: 12px; }
  .contact__item {
    display: flex; align-items: center; gap: 14px;
    font-size: 20px; letter-spacing: 1px; height: 31px; white-space: nowrap;
  }
  .contact__label { color: var(--gold); width: 16px; flex: none; }
  .icon { width: 22px; height: 22px; flex: none; }
</style>
</head>
<body>
  <section class="card card--front">
    <div class="brand">
      <span class="brand__mark"></span>
      <span class="brand__name">Harbourline<br>Property Group</span>
    </div>
    <div class="web-row">
      <span class="web-row__rule web-row__rule--left"></span>
      <span class="web-row__url">www.harbourlinepg.com</span>
      <span class="web-row__rule web-row__rule--right"></span>
    </div>
  </section>

  <section class="card card--back">
    <div class="brand">
      <span class="brand__mark"></span>
      <span class="brand__name">Harbourline<br>Property Group</span>
    </div>
    <div class="divider"></div>
    <div class="contact">
      <p class="contact__name">Olivia Marsh</p>
      <p class="contact__role">Director<br>Licensed Real Estate Agent</p>
      <p class="contact__address">14 Wharf Terrace Mosman<br>NSW 2088</p>
      <ul class="contact__list">
        <li class="contact__item">
          <svg class="icon" viewBox="0 0 22 22" aria-hidden="true">
            <rect width="22" height="22" rx="4" fill="var(--gold)"/>
            <rect x="7" y="4" width="8" height="14" rx="1.5" fill="none" stroke="#fff" stroke-width="1.4"/>
            <circle cx="11" cy="15.5" r="0.9" fill="#fff"/>
          </svg>
          <span class="contact__label">M</span>
          <span>0400 118 902</span>
        </li>
        <li class="contact__item">
          <svg class="icon" viewBox="0 0 22 22" aria-hidden="true">
            <rect width="22" height="22" rx="4" fill="var(--gold)"/>
            <path d="M5 8c0-2 3-3 6-3s6 1 6 3v1h-3V8H8v1H5z" fill="#fff"/>
            <rect x="6" y="10" width="10" height="7" rx="1.5" fill="#fff"/>
          </svg>
          <span class="contact__label">P</span>
          <span>02 9960 4410</span>
        </li>
        <li class="contact__item">
          <svg class="icon" viewBox="0 0 22 22" aria-hidden="true">
            <rect width="22" height="22" rx="4" fill="var(--gold)"/>
            <rect x="7" y="4.5" width="8" height="5" fill="none" stroke="#fff" stroke-width="1.3"/>
            <rect x="4.5" y="9.5" width="13" height="6" rx="1" fill="#fff"/>
            <rect x="7" y="13.5" width="8" height="4" fill="#fff" stroke="var(--gold)" stroke-width="1"/>
          </svg>
          <span class="contact__label">F</span>
          <span>02 9960 4411</span>
        </li>
        <li class="contact__item">
          <svg class="icon" viewBox="0 0 22 22" aria-hidden="true">
            <rect width="22" height="22" rx="4" fill="var(--gold)"/>
            <rect x="4.5" y="6.5" width="13" height="9" fill="none" stroke="#fff" stroke-width="1.4"/>
            <path d="M4.5 6.5 11 12l6.5-5.5" fill="none" stroke="#fff" stroke-width="1.4"/>
          </svg>
          <span>info@harbourlinepg.com</span>
        </li>
        <li class="contact__item">
          <svg class="icon" viewBox="0 0 22 22" aria-hidden="true">
            <rect width="22" height="22" rx="4" fill="var(--gold)"/>
            <circle cx="11" cy="11" r="6.5" fill="none" stroke="#fff" stroke-width="1.4"/>
            <ellipse cx="11" cy="11" rx="2.8" ry="6.5" fill="none" stroke="#fff" stroke-width="1.2"/>
            <path d="M4.5 11h13" stroke="#fff" stroke-width="1.2"/>
          </svg>
          <span>www.harbourlinepg.com</span>
        </li>
      </ul>
    </div>
  </section>
</body>
</html>
```